Blog Banner Design Project: Wanderly Ledger

Looking for a new banner for my blog " Neville Ostrander's Wanderly Ledger" at http://www.wanderlyledger.net - and once design agreed also want an updated album art for the podcast that goes along with the site.
For more about the blog and what it is about:
http://www.wanderlyledger.net/about
Wanderly Ledger is a Luxury Travel Blog And Podcast that provides inspiration, advice and tips about luxurious travel experiences, including destinations, transportation, accommodation, and journeys, that travellers can read, listen to or watch.
Objective of the new design
(1) retain the colour scheme ideally to retain the brand identity, as have been using these colours since 2005.
(2) introduce more of my personality and make it more visually and overt that it is "Neville Ostrander's Wanderly Ledger", so possibly introducing my image into the blog banner so visitors are clear and more aware of the person behind the brand.
(3) needs to have an up-market, luxury but modern feel.
(4) if possible reflect the focus on the content (destinations, transportation, accommodation, attractions and journeys) - but this maybe best left to just words as want the design to be bold and more of the branding and personality.
Ideal wording
Smallish: Neville Ostrander's
Main wording: Wanderly Ledger
Sub-title/ small: luxurious destinations, transportation, accommodation and journeys.
I have a poll running with readers of my blog to rate the designs to help me to chose the final route, and so there is no need to submit any more designs. I will make the decision once the poll closes on the weekend.

```html
<!DOCTYPE html>
<html lang="en">
<head>
<meta charset="utf-8">
<title>About – Neville Ostrander's Wanderly Ledger</title>
<link rel="stylesheet" href="https://fonts.googleapis.com/css2?family=Open+Sans:wght@300;400;600;700;800&family=PT+Sans+Narrow:wght@700&display=swap">
<style>
  :root {
    --purple: #5e2a86;
    --purple-deep: #3d1f6e;
    --orange: #f39224;
    --orange-light: #f7a840;
    --title-purple: #8a2a8c;
    --white: #ffffff;
    --ink: #444444;
    --nav-ink: #222222;
    --band-grey: #bdbdbd;
    --band-grey-light: #c9c9c9;
    --sidebar-ink: #4a4a4a;
    --chip: #9a9a9a;
  }
  * { box-sizing: border-box; margin: 0; padding: 0; }
  html, body { width: 1200px; height: 1000px; overflow: hidden; background: #fdfdfd; }
  body { position: relative; font-family: "Open Sans", sans-serif; }

  .banner {
    position: absolute; left: 22px; top: 159px; width: 1156px; height: 166px;
    background: linear-gradient(180deg, var(--purple-deep) 0%, var(--purple) 30%, #a5507a 52%, var(--orange) 72%, var(--orange-light) 100%);
    overflow: hidden; border: 1px solid #4a3060;
  }
  .banner__portrait {
    position: absolute; left: 29px; top: 9px; width: 176px; height: 176px;
    border-radius: 50%; border: 5px solid var(--white);
    background: linear-gradient(180deg, #2bb5ea 0%, #7fd3f2 55%, #3a3f4a 100%);
  }
  .banner__scene { position: absolute; left: 708px; top: 0; width: 448px; height: 166px; }
  .banner__title {
    position: absolute; left: 210px; top: 8px;
    font-weight: 800; font-size: 55px; color: var(--white); line-height: 1; letter-spacing: -0.5px;
  }
  .banner__owner {
    position: absolute; left: 214px; top: 74px;
    font-family: "PT Sans Narrow", sans-serif; font-weight: 700; font-size: 48px;
    color: var(--title-purple); line-height: 1;
  }
  .banner__tagline {
    position: absolute; left: 215px; top: 134px; z-index: 1;
    font-weight: 700; font-size: 17.5px; color: var(--white); letter-spacing: -0.3px; white-space: nowrap;
  }

  .nav { position: absolute; top: 328px; left: 0; width: 1200px; height: 24px; }
  .nav a { position: absolute; font-weight: 300; font-size: 19px; color: var(--nav-ink); text-decoration: none; }

  .page-band {
    position: absolute; left: 24px; top: 350px; width: 1156px; height: 85px;
    background: radial-gradient(ellipse at 55% 40%, var(--band-grey-light), var(--band-grey) 70%, #b3b3b3);
  }
  .page-band h1 { position: absolute; left: 12px; top: 8px; font-weight: 300; font-size: 48px; color: var(--white); }

  .content {
    position: absolute; left: 24px; top: 435px; width: 793px; height: 411px; overflow: hidden;
    border-left: 1px solid #e4e4e4; box-shadow: 6px 0 10px -6px rgba(0,0,0,0.12);
    background: #fdfdfd;
  }
  .content__body { padding: 47px 0 0 12px; width: 780px; font-size: 14px; line-height: 24px; color: var(--ink); white-space: nowrap; }
  .content__body p { margin-bottom: 24px; }
  .content__body strong { font-weight: 700; }

  .sidebar { position: absolute; left: 846px; top: 478px; width: 334px; }
  .sidebar h2 { font-weight: 300; font-size: 27px; color: var(--sidebar-ink); line-height: 1.2; }
  .follow { display: flex; gap: 16px; margin-top: 18px; height: 36px; align-items: center; }
  .follow a { display: flex; align-items: center; gap: 6px; font-size: 13px; color: var(--ink); text-decoration: none; }
  .follow i { display: block; width: 12px; height: 12px; background: var(--chip); }
  .sidebar .advert-title { margin-top: 56px; }
  .advert {
    position: absolute; left: 915px; top: 672px; width: 187px; height: 174px;
    background: linear-gradient(180deg, #0c168f 0%, #081060 60%, #3a1a08 85%, #d98a2a 100%);
  }
</style>
</head>
<body>
  <header class="banner">
    <div class="banner__portrait" role="img" aria-label="Portrait photo of Neville Ostrander"></div>
    <svg class="banner__scene" viewBox="0 0 448 166" role="img" aria-label="Tropical lagoon with overwater bungalows, palms and beach loungers">
      <defs>
        <linearGradient id="lagoon" x1="0" y1="0" x2="0" y2="1">
          <stop offset="0" stop-color="#7fb4e2"/>
          <stop offset="0.45" stop-color="#2fa6b8"/>
          <stop offset="0.75" stop-color="#6d8a52"/>
          <stop offset="1" stop-color="#e6dcc8"/>
        </linearGradient>
      </defs>
      <path d="M0 20 Q60 0 130 6 Q230 18 300 34 Q380 60 448 70 L448 166 L140 166 Q60 150 20 120 Q0 100 0 80 Z" fill="url(#lagoon)"/>
    </svg>
    <div class="banner__title">Wanderly Ledger</div>
    <div class="banner__owner">Neville Ostrander's</div>
    <div class="banner__tagline">luxurious destinations, transportation, accommodation and journeys.</div>
  </header>

  <nav class="nav">
    <a href="#" style="left:817px">Home</a>
    <a href="#" style="left:906px">About</a>
    <a href="#" style="left:996px">Top 10s</a>
    <a href="#" style="left:1101px">Podcast</a>
  </nav>

  <div class="page-band"><h1>About</h1></div>

  <main class="content">
    <div class="content__body">
      <p><strong>What is Wanderly Ledger about?</strong></p>
      <p>Wanderly Ledger Luxury Travel Blog And Podcast</p>
      <p>Wanderly Ledger provides inspiration, advice and tips about luxurious travel experiences, including<br>destinations, transportation, accommodation, attractions and journeys, that you can read, listen to or<br>watch.</p>
      <p>It is for travelers who have the budget to indulge in a luxurious travel experience, and are seeking<br>inspiration and recommendations. They are interested in the hottest and must-see and do, rather than the<br>unusual, off-the-beaten track and uncharted.</p>
      <p><strong>We focus on 5 main topic areas: destinations, transportation, accommodation, attractions and<br>journeys.</strong></p>
      <p>Wanderly Ledger provides honest and informative features, hosted by a seasoned traveler with</p>
    </div>
  </main>

  <aside class="sidebar">
    <h2>Follow On:</h2>
    <div class="follow">
      <a href="#"><i></i>Orrinet</a>
      <a href="#"><i></i>Calloway</a>
      <a href="#"><i></i>Pellum</a>
    </div>
    <h2 class="advert-title">Support Our Advertiser</h2>
  </aside>
  <div class="advert" role="img" aria-label="Advertiser photo of a resort roofline lit at night"></div>
</body>
</html>
```